2021 Summer Ads Hollis Bay Custom Homes

We need a re-design of our summer ad run for our customer, Hollis Bay Custom Homes. They are custom home builders in the mostly rural parts of West Virginia, USA. They are known for their "Forever Home" tagline. We'd like two designed ads with the main difference being just the custom home that's featured. These designs should be for a Zintrola banner like 300 x 250 and square ad like 250 x 250. For inspiration please visit the Hollis Bay Custom Homes website at www dot hollisbaycustomhomes dot com

Target Market(s)

consumers / new home shoppers

Industry/Entity Type

Consumer

Requirements
Must have
• HBCH logo
Price Lock Available!
Custom home pic
Learn more >
small CFRM logo mark

```html
<!DOCTYPE html>
<html lang="en">
<head>
<meta charset="utf-8">
<title>Hollis Bay Custom Homes – Summer Ad</title>
<link href="https://fonts.googleapis.com/css2?family=Montserrat:wght@600;700;800;900&display=swap" rel="stylesheet">
<style>
  :root {
    --navy: #1e2330;
    --navy-deep: #161a24;
    --red: #e5233a;
    --red-dark: #b8162a;
    --white: #ffffff;
    --sky-top: #6f7ea3;
    --sky-low: #c9a3b8;
    --house: #e9e6e0;
    --trees: #3a4a3c;
  }
  * { margin: 0; padding: 0; box-sizing: border-box; }
  html, body {
    width: 1200px; height: 1200px; overflow: hidden;
    background: var(--navy);
    font-family: "Montserrat", Arial, sans-serif;
  }
  .ad {
    position: relative; width: 1200px; height: 1200px;
    background: var(--navy); overflow: hidden;
  }
  .ad__photo {
    position: absolute; left: 0; top: 0; width: 1200px; height: 760px;
    background:
      linear-gradient(180deg, rgba(0,0,0,0) 55%, rgba(20,30,22,0.55) 100%),
      radial-gradient(ellipse at 55% 55%, rgba(255,236,200,0.55) 0%, rgba(255,236,200,0) 45%),
      linear-gradient(90deg, var(--trees) 0%, rgba(58,74,60,0) 18%, rgba(58,74,60,0) 82%, var(--trees) 100%),
      linear-gradient(180deg, var(--sky-top) 0%, var(--sky-low) 35%, var(--house) 55%, #8e8a80 80%, #4d5446 100%);
  }
  .ad__wave {
    position: absolute; left: 0; top: 560px; width: 1200px; height: 640px;
  }
  .brand {
    position: absolute; left: 60px; top: 775px;
    display: flex; align-items: center; gap: 18px;
    color: var(--white); font-weight: 800; font-size: 34px;
    letter-spacing: 1px; text-transform: uppercase; line-height: 1.05;
  }
  .brand__mark {
    width: 40px; height: 40px; background: var(--white);
  }
  .headline {
    position: absolute; left: 60px; top: 862px;
    font-weight: 900; font-size: 80px; line-height: 78px;
    text-transform: uppercase; color: var(--white); letter-spacing: 0.5px;
  }
  .headline__accent { color: var(--red); display: block; }
  .headline__line { display: block; }
  .offer {
    position: absolute; left: 60px; top: 1112px;
    font-weight: 700; font-size: 42px; color: var(--white);
    text-transform: uppercase; letter-spacing: 1px;
  }
  .partner {
    position: absolute; left: 870px; top: 870px; width: 290px;
    color: var(--white);
  }
  .partner__name {
    display: flex; align-items: center; gap: 14px;
    font-weight: 900; font-size: 60px; line-height: 1;
  }
  .partner__mark { width: 34px; height: 34px; background: var(--white); }
  .partner__caption {
    margin-top: 10px; font-weight: 600; font-size: 20px; line-height: 24px;
  }
  .cta {
    position: absolute; left: 795px; top: 1050px; width: 375px; height: 100px;
    border-radius: 50px; background: var(--red);
    color: var(--white); font-weight: 800; font-size: 36px;
    display: flex; align-items: center; justify-content: center;
    text-transform: uppercase; letter-spacing: 1px; text-decoration: none;
  }
</style>
</head>
<body>
<main class="ad">
  <div class="ad__photo" role="img" aria-label="Photo of a large white custom home at dusk with a metal roof, lit wraparound screened porch, stone pillars and a wooden deck, surrounded by trees"></div>

  <svg class="ad__wave" viewBox="0 0 1200 640" preserveAspectRatio="none" aria-hidden="true">
    <path d="M0 115 C 300 130, 600 150, 800 110 C 950 80, 1080 50, 1200 45 L1200 640 L0 640 Z" fill="var(--red)"/>
    <path d="M0 115 C 300 130, 600 155, 820 140 C 980 128, 1100 95, 1200 90 L1200 640 L0 640 Z" fill="var(--red-dark)"/>
    <path d="M0 110 C 250 125, 520 145, 700 140 C 900 133, 1060 120, 1200 112 L1200 640 L0 640 Z" fill="var(--navy)"/>
  </svg>

  <div class="brand">
    <span class="brand__mark" aria-hidden="true"></span>
    <span>Hollis Bay<br>Custom Homes</span>
  </div>

  <h1 class="headline">
    <span class="headline__accent">Start Building</span>
    <span class="headline__line">Your Forever</span>
    <span class="headline__line">Home Today!</span>
  </h1>

  <p class="offer">Price Lock Available!</p>

  <div class="partner">
    <div class="partner__name"><span>CFRM</span><span class="partner__mark" aria-hidden="true"></span></div>
    <p class="partner__caption">Council of Fine<br>Residential Makers</p>
  </div>

  <a class="cta" href="#">Learn More</a>
</main>
</body>
</html>
```